New Zealand Marlborough Sauvignon Blanc wine packaging design

We need packaging design for our new wine brand, Dunmore Vale. The wine is a New Zealand Marlborough Sauvignon Blanc. We would like the packaging will portray elegance and style with an understated label. We are looking for a label that portrays the elegance of the French Riviera. The label should be round or pill shaped.
Updates

Industry/Entity Type

Wine

Font styles to use
Serif
Sans Serif

Requirements
Must have
• The words in order of importance: Dunmore Vale, Sauvignon Blanc, Marlborough, New Zealand. It should be fit to the bottle posted in the links
Nice to have
• a pill shape or circular shape
Should not have
• Illustrations of wine bottles, wine glasses, or grapes

```html
<!DOCTYPE html>
<html lang="en">
<head>
<meta charset="utf-8">
<title>Dunmore Vale – Sauvignon Blanc Label</title>
<link rel="stylesheet" href="https://fonts.googleapis.com/css2?family=Playfair+Display:wght@500&family=Montserrat:wght@500&display=swap">
<style>
  :root {
    --backdrop: #000000;
    --label-white: #ffffff;
    --sky-teal: #1fa2c3;
    --sky-blue: #3fb0c6;
    --sunset-orange: #f08a3c;
    --sunset-peach: #f7b06a;
    --sea-teal: #2ab5c6;
    --sea-deep: #1b8fa6;
    --sand-light: #f4b98a;
    --sand-warm: #e98a5c;
    --shore-violet: #7a6a9e;
  }
  html, body {
    margin: 0;
    padding: 0;
    width: 705px;
    height: 1200px;
    overflow: hidden;
    background: var(--backdrop);
  }
  .label-stage {
    display: block;
    width: 705px;
    height: 1200px;
  }
  .brand-name {
    font-family: "Playfair Display", Georgia, serif;
    font-weight: 500;
    fill: var(--label-white);
    letter-spacing: 1px;
  }
  .ring-text {
    font-family: "Montserrat", Arial, sans-serif;
    font-weight: 500;
    font-size: 19px;
    letter-spacing: 7px;
    fill: var(--label-white);
  }
  .name-rule {
    stroke: var(--label-white);
    stroke-width: 2;
  }
</style>
</head>
<body>
<svg class="label-stage" viewBox="0 0 705 1200" xmlns="http://www.w3.org/2000/svg">
  <defs>
    <linearGradient id="riviera-scene" x1="0" y1="0" x2="0" y2="1">
      <stop offset="0" stop-color="var(--sky-teal)"/>
      <stop offset="0.2" stop-color="var(--sky-blue)"/>
      <stop offset="0.3" stop-color="var(--sunset-orange)"/>
      <stop offset="0.38" stop-color="var(--sunset-peach)"/>
      <stop offset="0.42" stop-color="var(--sunset-orange)"/>
      <stop offset="0.46" stop-color="var(--sea-teal)"/>
      <stop offset="0.6" stop-color="var(--sea-deep)"/>
      <stop offset="0.7" stop-color="var(--sand-light)"/>
      <stop offset="0.92" stop-color="var(--sand-warm)"/>
      <stop offset="1" stop-color="var(--shore-violet)"/>
    </linearGradient>
    <path id="ring-top" d="M 112,600 A 240 290 0 0 1 592,600"/>
    <path id="ring-bottom" d="M 108,600 A 244 292 0 0 0 596,600"/>
  </defs>

  <g class="wine-label">
    <ellipse class="label-scene" cx="352" cy="600" rx="252" ry="306"
             fill="url(#riviera-scene)" role="img"
             aria-label="Illustrated Riviera beach at sunset with sea, clouds, hillside villas, palms and striped umbrellas"/>

    <text class="ring-text">
      <textPath href="#ring-top" startOffset="50%" text-anchor="middle">SAUVIGNON BLANC</textPath>
    </text>

    <text class="brand-name" x="352" y="566" font-size="76" text-anchor="middle">DUNMORE</text>
    <text class="brand-name" x="352" y="646" font-size="76" text-anchor="middle">VALE</text>
    <line class="name-rule" x1="272" y1="688" x2="432" y2="688"/>

    <text class="ring-text">
      <textPath href="#ring-bottom" startOffset="50%" text-anchor="middle">NEW ZEALAND MARLBOROUGH</textPath>
    </text>
  </g>
</svg>
</body>
</html>
```